Frostvale Harborline LLC

we need a business card design

Industry/Entity Type

hvac

Contact Information for Business Card

my logo

Requirements
Must have
• my logo and same colors

```html
<!DOCTYPE html>
<html lang="en">
<head>
<meta charset="utf-8">
<title>Frostvale Harborline LLC — Business Card</title>
<link href="https://fonts.googleapis.com/css2?family=Montserrat:wght@400;500;700&display=swap" rel="stylesheet">
<style>
  :root {
    --brand-blue: #1f5fa8;
    --brand-orange: #f5a623;
    --card-white: #ffffff;
    --ink: #2b2b2b;
    --backdrop: #e9e7e3;
  }
  * { margin: 0; padding: 0; box-sizing: border-box; }
  html, body {
    width: 1200px; height: 931px; overflow: hidden;
    background: var(--backdrop);
    font-family: "Montserrat", sans-serif;
  }
  .card {
    position: absolute;
    left: 280px;
    width: 640px; height: 366px;
    background: var(--card-white);
    border-radius: 22px;
    box-shadow: 0 6px 18px rgba(0,0,0,0.18);
    overflow: hidden;
  }
  .card--front { top: 70px; }
  .card--back { top: 492px; }

  .brand-mark {
    display: flex; align-items: center; gap: 12px;
    color: var(--brand-blue);
    font-weight: 700;
    line-height: 1.1;
  }
  .brand-mark__dot {
    flex: none;
    border-radius: 50%;
    background: var(--brand-blue);
  }
  .card--front .brand-mark {
    position: absolute; left: 0; right: 0; top: 0; bottom: 0;
    justify-content: center;
    font-size: 34px;
  }
  .card--front .brand-mark__dot { width: 46px; height: 46px; }

  .card--back .brand-mark {
    position: absolute; right: 40px; top: 46px;
    font-size: 24px;
    width: 280px;
  }
  .card--back .brand-mark__dot { width: 34px; height: 34px; }

  .divider {
    position: absolute; left: 40px; right: 40px; top: 196px;
    height: 1.5px; background: var(--brand-blue);
  }
  .person {
    position: absolute; left: 40px; top: 132px;
  }
  .person__name {
    font-size: 30px; font-weight: 700; color: var(--brand-blue);
    line-height: 1.05;
  }
  .person__title {
    font-size: 16px; font-weight: 400; color: var(--ink);
    margin-top: 4px;
  }
  .contacts {
    position: absolute; left: 40px; top: 218px;
    list-style: none;
  }
  .contacts li {
    display: flex; align-items: center; gap: 12px;
    font-size: 16px; color: var(--ink);
    height: 32px;
  }
  .contacts svg { width: 18px; height: 18px; flex: none; }
  .address {
    position: absolute; right: 40px; top: 212px;
    text-align: right;
    font-size: 14px; color: var(--ink); line-height: 1.35;
  }
</style>
</head>
<body>

<section class="card card--front" aria-label="Card front">
  <div class="brand-mark">
    <span class="brand-mark__dot"></span>
    <span class="brand-mark__name">Frostvale Harborline LLC</span>
  </div>
</section>

<section class="card card--back" aria-label="Card back">
  <div class="brand-mark">
    <span class="brand-mark__dot"></span>
    <span class="brand-mark__name">Frostvale Harborline LLC</span>
  </div>

  <div class="person">
    <p class="person__name">Dana Whitlock</p>
    <p class="person__title">Managing Director</p>
  </div>

  <div class="divider"></div>

  <ul class="contacts">
    <li>
      <svg viewBox="0 0 18 18" aria-hidden="true"><rect x="4" y="1" width="10" height="16" rx="2" fill="none" stroke="#f5a623" stroke-width="1.8"/><circle cx="9" cy="14" r="1" fill="#f5a623"/></svg>
      +1 (555) 014-2290
    </li>
    <li>
      <svg viewBox="0 0 18 18" aria-hidden="true"><rect x="1" y="4" width="16" height="11" rx="1.5" fill="#f5a623"/><path d="M1.5 4.5 L9 10 L16.5 4.5" fill="none" stroke="#fff" stroke-width="1.4"/></svg>
      info@frostvaleharbor.com
    </li>
    <li>
      <svg viewBox="0 0 18 18" aria-hidden="true"><circle cx="9" cy="9" r="7.5" fill="#f5a623"/><ellipse cx="9" cy="9" rx="3.2" ry="7.5" fill="none" stroke="#fff" stroke-width="1.1"/><line x1="1.5" y1="9" x2="16.5" y2="9" stroke="#fff" stroke-width="1.1"/></svg>
      www.frostvaleharbor.com
    </li>
  </ul>

  <p class="address">48 Alder Lane,<br>Ridgeport, NY 13201</p>
</section>

</body>
</html>
```